Print Ad for a Human Resource Company

Hi.
Apologies for the quick turnaround but I just was brought on board to handle this project. The publication is Harbor Crest Journal, a Hawaii Business & Lifestyle publication.
Their upcoming issue will feature HR companies & of course we want our ad to stand out from the rest & make the phone ring.

Size: Vertical Ad 2.5" x 9.875

Color: 4 color, non bleed

Format: Hi-res (300 dpi) pdf
Ad Due: Drop dead dealine is Friday, 1/04/2013

Color: 4 color, non bleed

Reason: There is a God in heaven. We have a stay on the deadline to January 4th.

Target Market(s)

Small companies that benefit from having experts handle these areas.

Industry/Entity Type

Business

Requirements
Must have
• Copy:
Tagline: Keeping It Simple
Accounting
Human Resources
Payroll Services
Employee Benefits
Commercial Insurance
Personal Insurance
No Hidden Fees

Photos of both owners:
Marisol Ventanilla, CEO
Kara Whitlow, President

Company logo
Address: 512 Coral Mill Service Lane, Suite #214
Honolulu, HI 96819
Phone: 808.555.3172
BrightLedgerHelp.example
Nice to have
• This is a small locally owned firm owned by 2 local, very smart, sophisticated yet approachable, hardworking women. Their colors are Black background, silver type. The ad should be a reflection of their personalities.

```html
<!DOCTYPE html>
<html lang="en">
<head>
<meta charset="utf-8">
<title>BrightLedger – Vertical Print Ad</title>
<link rel="stylesheet" href="https://fonts.googleapis.com/css2?family=Abel&family=Saira+Condensed:wght@400;600&display=swap">
<style>
  :root {
    --page-bg: #1f1f1f;
    --brown: #8a5227;
    --brown-dark: #6e3f1c;
    --tan: #e9b965;
    --orange: #f2a446;
    --orange-deep: #d9853a;
    --rust: #c06e31;
    --panel: #e7e4a4;
    --mustard: #dcc45a;
    --cream: #f6e2b4;
    --ink: #3c2a1a;
    --white: #ffffff;
    --photo-top: linear-gradient(160deg, #5b4236 0%, #2a1f1c 55%, #1a1414 100%);
    --photo-bottom: linear-gradient(170deg, #d8c457 0%, #7c6a4a 45%, #1c1818 100%);
  }
  html, body {
    margin: 0;
    width: 1200px;
    height: 900px;
    overflow: hidden;
    background: var(--page-bg);
  }
  .ad {
    position: absolute;
    left: 493px;
    top: 30px;
    width: 213px;
    height: 840px;
    background: var(--tan);
    overflow: hidden;
    font-family: "Abel", sans-serif;
  }
  .ad > * { position: absolute; }
  .header-shapes { left: 0; top: 0; width: 213px; height: 215px; }
  .owner-photo {
    background: var(--photo-top);
  }
  .owner-photo--top { left: 0; top: 0; width: 128px; height: 207px; clip-path: polygon(0 0, 100% 0, 100% 100%, 0 100%); }
  .brand-bar {
    left: 17px; top: 145px; width: 196px; height: 34px;
    background: var(--brown);
    display: flex; align-items: center; justify-content: center;
  }
  .brand-name {
    font-family: "Saira Condensed", sans-serif;
    font-weight: 600;
    color: var(--white);
    font-size: 25px;
    letter-spacing: 1px;
    text-transform: uppercase;
  }
  .side-stripes { left: 0; top: 205px; width: 34px; height: 460px; }
  .tagline {
    left: 34px; top: 210px; width: 179px;
    text-align: center;
    color: var(--ink);
    font-size: 16px;
    letter-spacing: 0.8px;
  }
  .services-panel {
    left: 34px; top: 247px; width: 179px; height: 243px;
    background: var(--panel);
  }
  .services {
    list-style: none; margin: 0; padding: 18px 0 0 14px;
    color: var(--ink);
    font-family: "Saira Condensed", sans-serif;
    font-size: 16.5px;
    line-height: 24.4px;
  }
  .services li::before { content: "\25C6"; font-size: 12px; margin-right: 3px; vertical-align: 1px; }
  .fees-tag {
    left: 0; top: 436px; width: 166px; height: 30px;
    background: var(--brown);
    color: var(--white);
    font-family: "Saira Condensed", sans-serif;
    font-weight: 600;
    font-size: 17px;
    display: flex; align-items: center; justify-content: flex-end;
    padding-right: 12px; box-sizing: border-box;
  }
  .lower-panel { left: 34px; top: 496px; width: 179px; height: 170px; background: var(--mustard); }
  .owner-photo--bottom { left: 44px; top: 520px; width: 169px; height: 140px; background: var(--photo-bottom); }
  .contact {
    left: 0; top: 658px; width: 213px; height: 182px;
    background: var(--brown);
    text-align: center;
    color: var(--cream);
    font-family: "Saira Condensed", sans-serif;
  }
  .contact .brand-name { display: block; font-size: 26px; line-height: 30px; margin-top: 0; }
  .address { font-size: 18.5px; line-height: 32px; margin: 4px 0 0; font-style: normal; }
  .phone { font-size: 21px; margin: 4px 0 0; }
  .web { font-size: 17.5px; margin: 8px 0 0; }
</style>
</head>
<body>
<main class="ad">
  <svg class="header-shapes" viewBox="0 0 213 215" aria-hidden="true">
    <polygon points="0,0 125,0 140,150 0,150" fill="var(--brown)"/>
    <polygon points="0,175 213,175 213,182 0,212" fill="var(--brown)"/>
  </svg>
  <div class="owner-photo owner-photo--top" role="img" aria-label="Portrait photo of Marisol Ventanilla, CEO"></div>
  <div class="brand-bar"><span class="brand-name">BrightLedger</span></div>

  <svg class="side-stripes" viewBox="0 0 34 460" preserveAspectRatio="none" aria-hidden="true">
    <rect x="0" y="0" width="7" height="460" fill="var(--tan)"/>
    <rect x="7" y="0" width="12" height="460" fill="var(--orange)"/>
    <rect x="19" y="0" width="6" height="460" fill="var(--orange-deep)"/>
    <rect x="25" y="0" width="9" height="460" fill="var(--rust)"/>
  </svg>

  <p class="tagline" style="margin:0">Keeping It Simple</p>

  <section class="services-panel">
    <ul class="services">
      <li>Accounting</li>
      <li>Human Resources</li>
      <li>Payroll Services</li>
      <li>Employee Benefits</li>
      <li>Commercial Insurance</li>
      <li>Personal Insurance</li>
    </ul>
  </section>
  <div class="fees-tag">No Hidden Fees</div>

  <div class="lower-panel"></div>
  <div class="owner-photo owner-photo--bottom" role="img" aria-label="Portrait photo of Kara Whitlow, President"></div>

  <footer class="contact">
    <span class="brand-name">BrightLedger</span>
    <address class="address">512 Coral Mill Service Lane,<br>Suite #214, Honolulu, HI 96819</address>
    <p class="phone">Phone: 808.555.3172</p>
    <p class="web">BrightLedgerHelp.example</p>
  </footer>
</main>
</body>
</html>
```